R7M Horizon Business Card Design

We need a business card created for our New Business "R7M Horizon"<br/><br/>The business card design is up to you however the following information must be on the business card:<br/><br/>Front of the business card -<br/>Email :darrenp@r7mhorizon.nz<br/>Mobile: +64 (0) 22 4870 619<br/>Website: www.r7mhorizon.nz<br/>Card Owner Name: Darren Paltrow<br/>Company Title: Business Development Manager<br/>Slogan: "The BEST of both worlds". <br/>Logo On the front attached to the design brief<br/><br/>On the back: <br/>Space on the back for 4 more versions of the logo across the bottom of the card indicating different subsidiary brands - R7M Coffee, R7M Arts, R7M ?? (The card will be used for all of these brands - We Will add the extra subsidiary logos to the design once the design is finished (We are a graphics design team). <br/><br/>Other than that we want a premium feeling logo that remains universally usable depending on the business entity that we are using the card for. The use of bright bold colours would be great but we still want the card to feel premium.
Target Market(s)
Gift Design and Manufacturing Companies
Contact Information for Business Card
Front of the business card -
Email :darrenp@r7mhorizon.nz
Mobile: +64 (0) 22 4870 619
Website: www.r7mhorizon.nz
Card Owner Name: Darren Paltrow
Company Title: Business Development Manager
Slogan: "The BEST of both worlds".
Logo On the front attached to the design brief

```html
<!DOCTYPE html>
<html lang="en">
<head>
<meta charset="utf-8">
<title>R7M Horizon Business Card</title>
<link href="https://fonts.googleapis.com/css2?family=Montserrat:wght@600;700&family=Arimo:wght@400&display=swap" rel="stylesheet">
<style>
  :root {
    --backdrop: #3a332f;
    --card: #121212;
    --card-edge: #1c1c1c;
    --brand-blue: #3d4fc4;
    --silver: #d2d2d2;
    --text-light: #e6e6e6;
    --divider: #3a3a3a;
  }
  * { box-sizing: border-box; margin: 0; padding: 0; }
  html, body {
    width: 1200px; height: 844px; overflow: hidden;
    background: var(--backdrop);
  }
  .canvas {
    position: relative; width: 1200px; height: 844px;
    display: flex; align-items: center; justify-content: center; gap: 60px;
  }
  .card {
    position: relative; width: 530px; height: 303px;
    background: var(--card);
    border: 1px solid var(--card-edge);
    box-shadow: 0 14px 30px rgba(0,0,0,0.45);
  }

  /* Front */
  .front .brand {
    position: absolute; left: 36px; top: 152px;
  }
  .brand-name {
    font-family: "Montserrat", sans-serif; font-weight: 700;
    font-size: 26px; letter-spacing: 0.5px; line-height: 1;
    white-space: nowrap;
  }
  .front .brand-name { color: var(--brand-blue); }
  .front .divider {
    position: absolute; left: 262px; top: 70px; width: 1px; height: 170px;
    background: var(--divider);
  }
  .contact {
    position: absolute; left: 282px; top: 82px;
    font-family: "Arimo", sans-serif; color: var(--text-light);
  }
  .contact-name {
    font-family: "Montserrat", sans-serif; font-weight: 700;
    font-size: 17px; color: var(--brand-blue); letter-spacing: 0.5px;
    text-transform: uppercase;
  }
  .contact-title { font-size: 13px; margin-top: 3px; }
  .contact-list { list-style: none; margin-top: 18px; }
  .contact-list li {
    display: flex; align-items: center; gap: 8px;
    font-size: 13px; line-height: 22px;
  }
  .contact-list svg { width: 14px; height: 14px; flex: none; }

  /* Back */
  .back {
    display: flex; flex-direction: column; align-items: center; justify-content: center;
  }
  .back .brand-name { color: var(--silver); font-size: 40px; }
  .slogan {
    margin-top: 52px;
    font-family: "Montserrat", sans-serif; font-weight: 700;
    font-size: 12px; letter-spacing: 0.6px; color: var(--text-light);
    text-transform: uppercase;
  }
</style>
</head>
<body>
<main class="canvas">
  <section class="card front" aria-label="Business card front">
    <div class="brand">
      <span class="brand-name">R7M Horizon</span>
    </div>
    <div class="divider"></div>
    <div class="contact">
      <p class="contact-name">Darren Paltrow</p>
      <p class="contact-title">Business Development Manager</p>
      <ul class="contact-list">
        <li>
          <svg viewBox="0 0 16 16" aria-hidden="true"><rect x="1" y="1" width="14" height="14" rx="2" fill="none" stroke="#3d4fc4" stroke-width="1.4"/><path d="M5 4.5c0 4 2.5 6.5 6.5 7l.8-1.6-2-1-.9 1c-1.4-.6-2.3-1.5-2.9-2.9l1-.9-1-2z" fill="#3d4fc4"/></svg>
          +64 (0) 22 4870 619
        </li>
        <li>
          <svg viewBox="0 0 16 16" aria-hidden="true"><rect x="1" y="3" width="14" height="10" rx="1" fill="none" stroke="#3d4fc4" stroke-width="1.4"/><path d="M1.5 3.5 8 9l6.5-5.5" fill="none" stroke="#3d4fc4" stroke-width="1.4"/></svg>
          darrenp@r7mhorizon.nz
        </li>
        <li>
          <svg viewBox="0 0 16 16" aria-hidden="true"><circle cx="8" cy="8" r="6.5" fill="#3d4fc4"/><path d="M1.5 8h13M8 1.5c-3 3.5-3 9.5 0 13M8 1.5c3 3.5 3 9.5 0 13" fill="none" stroke="#121212" stroke-width="1"/></svg>
          www.r7mhorizon.nz
        </li>
      </ul>
    </div>
  </section>

  <section class="card back" aria-label="Business card back">
    <div class="brand">
      <span class="brand-name">R7M Horizon</span>
    </div>
    <p class="slogan">The Best of Both Worlds</p>
  </section>
</main>
</body>
</html>
```